International Petrochemical business needs a web design for Clearway Desk system

We need a web design for a "Clearway Desk" system for an international petrochemical company. The web site is used internally within the company. It is hosted by an internal department which provides government permit request service for other departments.

We would like to see designs of two pages using color light blue. (home page, internal page as attached).
Home Page:
1. Header has a background image and small animation. Header on home page can be taller than the header of the internal page.
2. Layout as attached.

Internal Page:
1. Header can use the same background image as the home page and can be shorter to utilize the page for content.
2. The blue icon behind every captions represent an icon. When user move mouse over this icon, it displays the caption in Thai language as a tooltip. This icon needs to be redesign.

The final design should communicate the followings:
- Excellent service provided system in terms of time and accurary
- Rapid growth of business via building petrochemical refinery plant
Updates

For Internal Page, the blue circle behind every captions represent an icon. When mouse over this icon, a tool tip showing the caption in Thai language is shown. Please also design this icon..

There are more feedbacks from customer as followed:

1. Banner should consists of 
    1.1 "Approved" stamp on paper
    1.2 An image of Garuda. It is used on every government documents in Thailand
    1.3 Image of petrochemical plant
2. Each menu item (Home, Permit, Search, etc) should have different colors. Drop down menu will use the same color as its parent menu item.
3. Overall tone of the web page should be light blue with background of the body the web page in white
4. "New Request" button should use green color with icon on it
5. Table header of each box in the body of the page should use dark blue background with text in white

Please kindly submit your revisions.
Thank you.

Industry/Entity Type

Business

Requirements
Must have
• 1. Design for 1024x768 screen resolution
2. Use light blue theme
3. Background of header where the company logo is must have white background

```html
<!DOCTYPE html>
<html lang="en">
<head>
<meta charset="utf-8">
<title>Clearway Desk System</title>
<link href="https://fonts.googleapis.com/css2?family=Cabin:wght@400;500;600&family=Questrial&display=swap" rel="stylesheet">
<style>
:root{
  --sky-top:#cfe6f6;
  --sky-mid:#e9f4fb;
  --sky-low:#b9daf1;
  --blue:#3d95ec;
  --blue-light:#72b6f6;
  --blue-dark:#1c78da;
  --navy:#1e1f6b;
  --red:#e3212b;
  --grey-text:#5a5d61;
  --panel:#3c3c3c;
  --panel-dark:#2f2f2f;
  --rule:#5b5b5b;
  --white:#ffffff;
  --table-head:#232323;
}
*{box-sizing:border-box;margin:0;padding:0}
html,body{width:1182px;height:1200px;overflow:hidden}
body{position:relative;font-family:"Cabin",sans-serif;color:var(--white);background:var(--white)}
.sky{position:absolute;left:0;top:0;width:1182px;height:1130px;
  background:radial-gradient(ellipse at 30% 20%,var(--sky-mid),transparent 60%),
  radial-gradient(ellipse at 80% 60%,var(--sky-mid),transparent 55%),
  linear-gradient(180deg,var(--sky-top) 0%,var(--sky-mid) 45%,var(--sky-low) 75%,var(--white) 100%)}
.abs{position:absolute}

/* brand */
.brand{left:131px;top:20px;display:flex;align-items:center;gap:8px}
.brand-dot{width:40px;height:40px;border-radius:50%;background:var(--blue-dark)}
.brand-name{font-family:"Cabin",sans-serif;font-weight:600;font-size:19px;line-height:19px;color:var(--blue-dark)}

/* navigation */
.nav{left:129px;top:88px;width:923px;height:36px;border-radius:5px;
  background:linear-gradient(180deg,var(--blue-light),var(--blue));display:flex;align-items:center}
.nav a{color:var(--white);text-decoration:none;font-size:15px;width:102px;text-align:center;height:36px;line-height:36px;border-right:1px dotted rgba(255,255,255,.45)}
.nav a:first-child{width:98px}
.search{position:absolute;left:632px;top:8px;width:282px;height:20px;background:var(--white);border:1px solid #bcd6ee;display:flex}
.search span{flex:1;font-size:11px;font-style:italic;color:#8a8f96;line-height:18px;padding-left:4px}
.search i{width:28px;border-left:1px solid #d0d8e0;display:flex;align-items:center;justify-content:center}

/* headline */
.headline{left:144px;top:202px;font-family:"Questrial",sans-serif;line-height:1}
.headline .l1{font-size:35px;color:var(--navy);letter-spacing:-0.5px}
.headline .l1 span{color:var(--grey-text)}
.headline .l2{font-size:26px;color:var(--grey-text);margin-top:4px}
.headline .l2 b{font-weight:400;font-size:43px;color:var(--red)}
.headline .l3{font-size:31px;color:var(--red);margin-top:4px}

.plant{left:601px;top:160px;width:448px;height:242px;
  background:linear-gradient(180deg,rgba(220,232,242,0) 0%,#c2c9d0 35%,#8a929c 75%,#5f656d 100%)}

/* panels */
.panel{background:linear-gradient(135deg,var(--panel),var(--panel-dark));border-radius:3px;box-shadow:0 8px 10px -6px rgba(0,0,0,.25)}
.ribbon{position:absolute;left:-4px;top:10px;height:29px;width:343px;
  background:linear-gradient(180deg,var(--blue-light),var(--blue));
  clip-path:polygon(0 0,100% 0,95% 100%,0 100%);
  font-size:16px;font-weight:500;line-height:29px;padding-left:17px;letter-spacing:-0.5px;text-transform:uppercase}
.panel-title{position:absolute;left:12px;top:10px;font-size:21px;font-weight:500;letter-spacing:-0.5px}
table{position:absolute;border-collapse:collapse;font-size:13px}
th{font-weight:400;font-size:16px;color:#d8d8d8;text-align:left;height:39px;letter-spacing:.5px}
td{height:38px;color:#eee}
th,td{border-bottom:1px dotted var(--rule);border-right:1px dotted var(--rule);padding-left:12px}
th:last-child,td:last-child{border-right:none}
td.c{padding-left:22px}

.pager{position:absolute;display:flex;align-items:center;gap:4px;font-size:15px;color:#8d8d8d}
.pager b{font-weight:400;color:var(--white)}
.pager .btn{width:16px;height:15px;background:#e6e6e6;display:flex;align-items:center;justify-content:center}
.pager .nums{letter-spacing:3px;margin:0 2px}

.new-req{left:129px;top:402px;width:456px;height:199px}
.working{left:597px;top:402px;width:455px;height:199px}
.progress{left:130px;top:849px;width:456px;height:255px}
.completed{left:628px;top:938px;width:404px;height:165px}

/* expiring */
.expiring{left:129px;top:625px;width:923px;height:194px;border-radius:4px;
  background:linear-gradient(180deg,var(--blue-light),var(--blue) 40%,var(--blue-dark));box-shadow:0 8px 10px -6px rgba(0,0,0,.2)}
.expiring .panel-title{top:10px;font-size:21px}
.expiring table{left:12px;top:42px;width:898px}
.expiring th{background:var(--table-head);color:var(--white);font-size:16px;height:38px;border:none;border-right:1px solid #444}
.expiring td{border-color:rgba(255,255,255,.35);color:var(--white)}
.expiring .pager{color:rgba(255,255,255,.7)}

/* call to action */
.cta{left:622px;top:851px;width:410px;height:60px;border-radius:3px;color:var(--white);text-decoration:none;
  background:linear-gradient(180deg,#f46a6e,var(--red) 55%,#c8161f);box-shadow:0 3px 0 #a51019}
.cta-tag{position:absolute;left:18px;top:-5px;width:64px;height:78px;background:#3a3a3a;
  clip-path:polygon(0 0,100% 0,100% 100%,50% 78%,0 100%);display:flex;justify-content:center;padding-top:12px}
.cta-label{position:absolute;left:98px;top:10px;font-size:37px;font-weight:600;letter-spacing:-1px;color:var(--white)}

/* footer */
.footer-rule{left:129px;top:1134px;width:923px;border-top:1px dashed #9aa0a6}
.copyright{left:131px;top:1159px;font-size:12px;color:#5a5d61;letter-spacing:-0.3px}
.foot-brand{left:928px;top:1150px;display:flex;align-items:center;gap:6px}
.foot-brand .brand-dot{width:26px;height:26px;background:#8f9398}
.foot-brand .brand-name{font-size:13px;line-height:13px;color:#7a7e83}
</style>
</head>
<body>
<div class="sky" role="img" aria-label="Soft blue sky with white clouds"></div>

<div class="abs brand"><span class="brand-dot"></span><span class="brand-name">NORTHBAY<br>PETROCHEMICAL</span></div>

<nav class="abs nav">
  <a href="#">Home</a><a href="#">Permits</a><a href="#">Search</a><a href="#">Report</a><a href="#">Admin</a><a href="#">Help</a>
  <div class="search"><span>Serch By Number...</span><i><svg width="16" height="16" viewBox="0 0 16 16"><circle cx="6.5" cy="6.5" r="4.5" fill="none" stroke="#555" stroke-width="2"/><line x1="10" y1="10" x2="14.5" y2="14.5" stroke="#555" stroke-width="2.4"/></svg></i></div>
</nav>

<div class="abs headline">
  <div class="l1">CLEARWAY DESK <span>SYSTEM</span></div>
  <div class="l2">for an <b>INTERNATIONAL</b></div>
  <div class="l3">PETROCHEMICAL COMPANY</div>
</div>

<div class="abs plant" role="img" aria-label="Petrochemical refinery plant with towers and pipework"></div>

<section class="abs panel new-req">
  <div class="ribbon">New Requests</div>
  <table style="left:12px;top:49px;width:431px">
    <tr><th style="width:114px">Request No.</th><th style="width:178px">Requested Date</th><th>Branch</th></tr>
    <tr><td class="c">56-0003</td><td class="c" style="padding-left:56px">20/4/2013</td><td class="c">GC1</td></tr>
    <tr><td class="c">56-0004</td><td class="c" style="padding-left:56px">21/4/2013</td><td class="c">GC2</td></tr>
  </table>
  <div class="pager" style="right:16px;top:173px"><span class="btn"><svg width="6" height="8"><polygon points="6,0 0,4 6,8" fill="#333"/></svg></span><span class="nums"><b>1</b> 2 3 4 5 6 7</span><span class="btn"><svg width="6" height="8"><polygon points="0,0 6,4 0,8" fill="#333"/></svg></span></div>
</section>

<section class="abs panel working">
  <div class="panel-title">MY WORKING REQUESTS</div>
  <table style="left:12px;top:41px;width:430px">
    <tr><th style="width:116px">Request No.</th><th style="width:164px">Requested Date</th><th>Status</th></tr>
    <tr><td class="c">55-0200</td><td class="c" style="padding-left:52px">25/3/2013</td><td>Waiting for process</td></tr>
    <tr><td class="c">55-0210</td><td class="c" style="padding-left:52px">23/3/2013</td><td>In progress</td></tr>
  </table>
  <div class="pager" style="right:16px;top:171px"><span class="btn"><svg width="6" height="8"><polygon points="6,0 0,4 6,8" fill="#333"/></svg></span><span class="nums"><b>1</b> 2 3 4 5 6 7</span><span class="btn"><svg width="6" height="8"><polygon points="0,0 6,4 0,8" fill="#333"/></svg></span></div>
</section>

<section class="abs expiring">
  <div class="panel-title">Expiring Permits</div>
  <table>
    <tr><th style="width:106px">Permit No.</th><th style="width:148px">Expire Date</th><th style="width:182px">Permit Name</th><th style="width:139px">Branch</th><th style="width:186px">Required Time (Day)</th><th>Due Date</th></tr>
    <tr><td>56-0003</td><td>20/4/2013</td><td>Permit Name ###10</td><td>GC1</td><td>30 Days</td><td>- 40 Days</td></tr>
    <tr><td>56-0004</td><td>21/4/2013</td><td>Permit Name ###10</td><td>GC2</td><td>60 Days</td><td>- 15 Days</td></tr>
  </table>
  <div class="pager" style="right:14px;top:167px"><span class="btn"><svg width="6" height="8"><polygon points="6,0 0,4 6,8" fill="#333"/></svg></span><span class="nums"><b>1</b> 2 3 4 5 6 7</span><span class="btn"><svg width="6" height="8"><polygon points="0,0 6,4 0,8" fill="#333"/></svg></span></div>
</section>

<section class="abs panel progress">
  <div class="ribbon">My In Progress Requests</div>
  <table style="left:12px;top:49px;width:431px">
    <tr><th style="width:114px">Request No.</th><th style="width:178px">Requested Date</th><th>Status</th></tr>
    <tr><td class="c">56-0001</td><td class="c" style="padding-left:56px">20/4/2013</td><td class="c">In progress</td></tr>
    <tr><td class="c">56-0002</td><td class="c" style="padding-left:56px">21/4/2013</td><td class="c">In progress</td></tr>
    <tr><td class="c">56-0002</td><td class="c" style="padding-left:56px">21/4/2013</td><td class="c">In progress</td></tr>
  </table>
  <div class="pager" style="right:16px;top:224px"><span class="btn"><svg width="6" height="8"><polygon points="6,0 0,4 6,8" fill="#333"/></svg></span><span class="nums"><b>1</b> 2 3 4 5 6 7</span><span class="btn"><svg width="6" height="8"><polygon points="0,0 6,4 0,8" fill="#333"/></svg></span></div>
</section>

<a class="abs cta" href="#">
  <span class="cta-tag"><svg width="30" height="30" viewBox="0 0 30 30"><path d="M6 3h12l6 6v18H6z" fill="none" stroke="#fff" stroke-width="2"/><path d="M18 3v6h6" fill="none" stroke="#fff" stroke-width="2"/><path d="M10 20l8-8 2 2-8 8h-2z" fill="#fff"/></svg></span>
  <span class="cta-label">NEW REQUESTS</span>
</a>

<section class="abs panel completed">
  <div class="ribbon" style="width:370px;text-transform:none;font-size:16px">Recent Completed Requests</div>
  <table style="left:13px;top:47px;width:378px">
    <tr><th style="width:157px">Request No.</th><th>Complete Date</th></tr>
    <tr><td>56-0001</td><td>20/4/2013</td></tr>
  </table>
  <div class="pager" style="right:18px;top:136px"><span class="btn"><svg width="6" height="8"><polygon points="6,0 0,4 6,8" fill="#333"/></svg></span><span class="nums"><b>1</b> 2 3 4 5 6 7</span><span class="btn"><svg width="6" height="8"><polygon points="0,0 6,4 0,8" fill="#333"/></svg></span></div>
</section>

<div class="abs footer-rule"></div>
<div class="abs copyright">Copyright © 2013 Northbay Petrochemical. All rights reserved.</div>
<div class="abs foot-brand"><span class="brand-dot"></span><span class="brand-name">NORTHBAY<br>PETROCHEMICAL</span></div>
</body>
</html>
```